Business card por a urban DJ, up scale audience target

Need a sober design, modern, conservative colors but i can consider some options, y play rnb, hip hop, EDM and top40.

Business card for contact and personal info, double sided, use logo attrached please; im 42 so i need a card acording to my age an target audience.

Target Market(s)

Adult people, up scale audience

Industry/Entity Type

Music Download

Contact Information for Business Card

Cel (318) 4207265518 www.lumadrift.com

Requirements
Must have
• open mind
Nice to have
• open mind
Should not have
• DJ

```html
<!DOCTYPE html>
<html lang="en">
<head>
<meta charset="utf-8">
<title>Lumadrift business card</title>
<link href="https://fonts.googleapis.com/css2?family=Open+Sans:wght@400;700&display=swap" rel="stylesheet">
<style>
  :root {
    --ink: #000000;
    --paper: #ffffff;
    --backdrop: #3a3a3a;
    --muted: #333333;
  }
  html, body {
    margin: 0;
    width: 1200px;
    height: 900px;
    overflow: hidden;
    background: var(--backdrop);
    font-family: "Open Sans", sans-serif;
  }
  .stage {
    position: relative;
    width: 1200px;
    height: 900px;
  }
  .card {
    position: absolute;
    left: 240px;
    width: 720px;
    height: 411px;
    overflow: hidden;
  }
  .card--front { top: 26px; background: var(--ink); color: var(--paper); }
  .card--back  { top: 463px; background: var(--paper); color: var(--ink); }

  .brand-name {
    font-weight: 700;
    letter-spacing: 6px;
    margin: 0;
    line-height: 1;
  }
  .card--front .brand-name {
    position: absolute;
    left: 330px;
    top: 92px;
    font-size: 110px;
    color: var(--paper);
  }
  .card--front .site {
    position: absolute;
    left: 336px;
    top: 222px;
    font-size: 24px;
    letter-spacing: 5px;
    color: var(--paper);
  }
  .equalizer { position: absolute; }
  .card--front .equalizer { left: 0; bottom: 0; }
  .card--back .equalizer { right: 0; bottom: 0; }

  .card--back .brand-name {
    position: absolute;
    left: 40px;
    top: 70px;
    font-size: 96px;
    color: var(--ink);
  }
  .rule {
    position: absolute;
    left: 0;
    right: 0;
    top: 226px;
    height: 2px;
    background: var(--ink);
  }
  .contact {
    position: absolute;
    left: 40px;
    top: 268px;
  }
  .contact .person { font-size: 26px; font-weight: 700; margin: 0; }
  .contact .role { font-size: 15px; margin: 0 0 8px; color: var(--muted); }
  .contact .line {
    display: flex;
    align-items: center;
    gap: 8px;
    font-size: 17px;
    margin: 2px 0;
  }
  .contact svg { width: 13px; height: 13px; }
</style>
</head>
<body>
<main class="stage">

  <section class="card card--front" aria-label="Card front">
    <h1 class="brand-name">LUMA</h1>
    <div class="site">www.lumadrift.com</div>
    <svg class="equalizer" width="440" height="90" viewBox="0 0 440 90" fill="#ffffff" aria-hidden="true">
      <rect x="4" y="40" width="9" height="50"/><rect x="17" y="55" width="9" height="35"/>
      <rect x="30" y="70" width="9" height="20"/><rect x="43" y="46" width="9" height="44"/>
      <rect x="56" y="76" width="9" height="14"/><rect x="69" y="62" width="9" height="28"/>
      <rect x="82" y="50" width="9" height="40"/><rect x="95" y="74" width="9" height="16"/>
      <rect x="108" y="80" width="9" height="10"/><rect x="121" y="84" width="9" height="6"/>
      <rect x="134" y="66" width="9" height="24"/><rect x="147" y="58" width="9" height="32"/>
      <rect x="160" y="72" width="9" height="18"/><rect x="173" y="54" width="9" height="36"/>
      <rect x="186" y="78" width="9" height="12"/><rect x="199" y="60" width="9" height="30"/>
      <rect x="212" y="70" width="9" height="20"/><rect x="225" y="48" width="9" height="42"/>
      <rect x="238" y="76" width="9" height="14"/><rect x="251" y="66" width="9" height="24"/>
      <rect x="264" y="82" width="9" height="8"/><rect x="277" y="56" width="9" height="34"/>
      <rect x="290" y="74" width="9" height="16"/><rect x="303" y="80" width="9" height="10"/>
      <rect x="316" y="62" width="9" height="28"/><rect x="329" y="76" width="9" height="14"/>
      <rect x="342" y="84" width="9" height="6"/><rect x="355" y="68" width="9" height="22"/>
      <rect x="368" y="80" width="9" height="10"/><rect x="381" y="72" width="9" height="18"/>
      <rect x="394" y="84" width="9" height="6"/><rect x="407" y="78" width="9" height="12"/>
      <rect x="420" y="86" width="9" height="4"/>
    </svg>
  </section>

  <section class="card card--back" aria-label="Card back">
    <h2 class="brand-name">LUMA</h2>
    <div class="rule"></div>
    <svg class="equalizer" width="400" height="160" viewBox="0 0 400 160" fill="#000000" aria-hidden="true">
      <rect x="2" y="142" width="9" height="18"/><rect x="15" y="128" width="9" height="32"/>
      <rect x="28" y="136" width="9" height="24"/><rect x="41" y="146" width="9" height="14"/>
      <rect x="54" y="120" width="9" height="40"/><rect x="67" y="138" width="9" height="22"/>
      <rect x="80" y="130" width="9" height="30"/><rect x="93" y="146" width="9" height="14"/>
      <rect x="106" y="112" width="9" height="48"/><rect x="119" y="134" width="9" height="26"/>
      <rect x="132" y="124" width="9" height="36"/><rect x="145" y="140" width="9" height="20"/>
      <rect x="158" y="104" width="9" height="56"/><rect x="171" y="126" width="9" height="34"/>
      <rect x="184" y="116" width="9" height="44"/><rect x="197" y="136" width="9" height="24"/>
      <rect x="210" y="96" width="9" height="64"/><rect x="223" y="120" width="9" height="40"/>
      <rect x="236" y="108" width="9" height="52"/><rect x="249" y="130" width="9" height="30"/>
      <rect x="262" y="84" width="9" height="76"/><rect x="275" y="110" width="9" height="50"/>
      <rect x="288" y="96" width="9" height="64"/><rect x="301" y="122" width="9" height="38"/>
      <rect x="314" y="72" width="9" height="88"/><rect x="327" y="100" width="9" height="60"/>
      <rect x="340" y="84" width="9" height="76"/><rect x="353" y="112" width="9" height="48"/>
      <rect x="366" y="58" width="9" height="102"/><rect x="379" y="88" width="9" height="72"/>
      <rect x="392" y="40" width="8" height="120"/>
    </svg>
    <div class="contact">
      <p class="person">Marco Vell</p>
      <p class="role">CEO</p>
      <p class="line">
        <svg viewBox="0 0 13 13" aria-hidden="true"><rect x="3" y="0.5" width="7" height="12" rx="1.2" fill="none" stroke="#000" stroke-width="1.2"/><rect x="5.3" y="10" width="2.4" height="1" fill="#000"/></svg>
        (318) 4207265518
      </p>
      <p class="line">
        <svg viewBox="0 0 13 13" aria-hidden="true"><circle cx="6.5" cy="6.5" r="5.8" fill="none" stroke="#000" stroke-width="1.1"/><ellipse cx="6.5" cy="6.5" rx="2.5" ry="5.8" fill="none" stroke="#000" stroke-width="1"/><line x1="0.7" y1="6.5" x2="12.3" y2="6.5" stroke="#000" stroke-width="1"/></svg>
        www.lumadrift.com
      </p>
    </div>
  </section>

</main>
</body>
</html>
```